Coastal Learner Bureau business cards

Australian company about to start offering its services. We recruit international students to come to study English, vocational education and postgraduate courses in Australia. We help them find the institution and select the right city they want to come to Australia. We are a young, online oriented and supportive agency. Our clients are between 18 and 35 years old, mainly University students, young professionals or people with work experience. We provide much more information that any other agency offer. We administrate a Facebook group with more than 11.000 members that daily ask questions about general information when coming to Australia, while they are here and even after they leave the country

Target Market(s)

International students from South America, Central America and Europe

Industry/Entity Type

Student

Contact Information for Business Card

Tomas Bilbrea
Managing Director
tomas@kelvarin.com.au
www.kelvoria.com.au
+61 491058264
Melbourne, Australia

Font styles to use
Serif
Sans Serif

Colors

Designer to choose colors to be used in the design.

Requirements
Must have
• Horizontal design
• Standard business card size and shape. If font uses green or yellow colours, they will have to match the ones from the logo
Nice to have
• UPDATE: Use the contents of the green image to design one of the card sides. Use our logo in the background of that side as watermark.
• Passport image, or immigration stamps. A picture of the Yarra River (from Melbourne) would be cool as well.
Should not have
• Non-standard business card size and shape
• Not black as the background colour of any sides as we are not a VIP agency or a hight class service. We are orientes to young people and they like colours, pictures, something attractive.
• Vertical design
• NO YELLOW or BLACK AS THE BACKGROUND COLOUR OF ANY SIDE OF THE BIZ CARD

```html
<!DOCTYPE html>
<html lang="en">
<head>
<meta charset="utf-8">
<title>Coastal Learner Bureau business cards</title>
<link rel="stylesheet" href="https://fonts.googleapis.com/css2?family=PT+Sans:wght@400;700&display=swap">
<style>
  :root {
    --page-bg: #e7e9e8;
    --green-light: #16895a;
    --green: #0e6b44;
    --green-dark: #0a5234;
    --gold: #d6b31d;
    --paper: #f6f6f4;
    --white: #ffffff;
    --shadow: rgba(0, 0, 0, 0.18);
  }
  * { box-sizing: border-box; margin: 0; padding: 0; }
  html, body {
    width: 1200px;
    height: 900px;
    overflow: hidden;
    background: var(--page-bg);
    font-family: "PT Sans", sans-serif;
  }
  .canvas {
    position: relative;
    width: 1200px;
    height: 900px;
  }
  .card {
    position: absolute;
    width: 660px;
    height: 377px;
    border-radius: 4px;
    overflow: hidden;
    box-shadow: 0 10px 28px var(--shadow);
  }
  /* Front side */
  .card-front {
    left: 120px;
    top: 50px;
    background: linear-gradient(135deg, var(--green-light) 0%, var(--green) 50%, var(--green-dark) 100%);
    color: var(--white);
  }
  .card-front .brand {
    position: absolute;
    left: 0;
    right: 0;
    top: 105px;
    text-align: center;
    font-weight: 700;
    font-size: 64px;
    letter-spacing: 1px;
    color: var(--white);
  }
  .card-front .tagline {
    position: absolute;
    left: 0;
    right: 0;
    top: 262px;
    display: flex;
    align-items: center;
    justify-content: center;
    gap: 12px;
    font-size: 15px;
    font-weight: 700;
  }
  .card-front .tagline::before,
  .card-front .tagline::after {
    content: "";
    width: 120px;
    height: 1px;
    background: rgba(255, 255, 255, 0.7);
  }
  .card-front .sheen {
    position: absolute;
    inset: 0;
  }
  /* Back side */
  .card-back {
    left: 420px;
    top: 470px;
    background: var(--paper);
  }
  .card-back .brand {
    position: absolute;
    left: 0;
    right: 0;
    top: 78px;
    text-align: center;
    font-weight: 700;
    font-size: 54px;
    letter-spacing: 1px;
    color: var(--green);
  }
  .band-gold {
    position: absolute;
    left: 0;
    right: 0;
    top: 196px;
    height: 64px;
    background: var(--gold);
    text-align: center;
    color: var(--white);
    padding-top: 10px;
  }
  .holder-name {
    font-weight: 700;
    font-size: 19px;
    letter-spacing: 0.5px;
    text-transform: uppercase;
  }
  .holder-role {
    font-size: 17px;
    letter-spacing: 0.5px;
    text-transform: uppercase;
  }
  .band-green {
    position: absolute;
    left: 0;
    right: 0;
    top: 260px;
    bottom: 0;
    background: linear-gradient(180deg, var(--green) 0%, var(--green-dark) 100%);
    color: var(--white);
    text-align: center;
    padding-top: 14px;
    font-size: 17px;
    line-height: 1.5;
  }
  .contact-web { letter-spacing: 3px; }
</style>
</head>
<body>
<main class="canvas">
  <section class="card card-front" aria-label="Front of business card">
    <svg class="sheen" width="660" height="377" viewBox="0 0 660 377" aria-hidden="true">
      <line x1="40" y1="370" x2="640" y2="160" stroke="rgba(255,255,255,0.25)" stroke-width="1"/>
    </svg>
    <div class="brand">Kelvoria</div>
    <p class="tagline">Hacemos más por ti!</p>
  </section>

  <section class="card card-back" aria-label="Back of business card">
    <div class="brand">Kelvoria</div>
    <div class="band-gold">
      <p class="holder-name">Tomas Bilbrea</p>
      <p class="holder-role">Managing Director</p>
    </div>
    <div class="band-green">
      <p class="contact-city">Melbourne, Australia</p>
      <p class="contact-lines">P: +61 491058264 &nbsp;E: tomas@kelvarin.com.au</p>
      <p class="contact-web">www.kelvoria.com.au</p>
    </div>
  </section>
</main>
</body>
</html>
```